Re-Design of a 1 Pager IT Security Website

Please create a 1 Pager design for this website and all its elements: http://www.quillstonebrightmarsh.com/

Colours, Fonts etc: You can select whatever you prefer

```html
<!DOCTYPE html>
<html lang="en">
<head>
<meta charset="utf-8">
<title>Domain Monitoring</title>
<link rel="stylesheet" href="https://fonts.googleapis.com/css2?family=Roboto:wght@400;500;700;900&display=swap">
<style>
:root{
  --navy:#21187a;
  --navy-deep:#160f5c;
  --cyan:#3ec3cf;
  --ink:#141414;
  --body:#4a4a4a;
  --lavender:#f1f1fb;
  --footer:#151515;
  --footer-base:#050505;
  --white:#ffffff;
}
*{margin:0;padding:0;box-sizing:border-box}
html,body{width:1200px;height:3811px;overflow:hidden}
body{position:relative;font-family:'Roboto',sans-serif;color:var(--ink);background:var(--white)}
.abs{position:absolute}

/* hero */
.hero{left:0;top:0;width:1200px;height:618px;background:linear-gradient(160deg,#2a1d86 0%,#1f1677 55%,#1a1270 100%);overflow:hidden}
.topbar{left:429px;top:0;width:771px;height:47px;background:var(--cyan);clip-path:polygon(0 0,100% 0,100% 100%,40px 100%)}
.topbar-item{top:0;height:47px;display:flex;align-items:center;gap:12px;color:var(--white);font-size:13px;font-weight:500}
.topbar-icon{width:32px;height:32px;border:1.5px solid rgba(255,255,255,.8);border-radius:50%;display:flex;align-items:center;justify-content:center}
.topbar-sep{left:806px;top:8px;width:1px;height:31px;background:rgba(255,255,255,.5)}
.brand{left:111px;top:37px;color:var(--white);font-size:25px;font-weight:700;letter-spacing:.2px}
.nav a{position:absolute;top:66px;color:var(--white);font-size:16px;font-weight:700;text-decoration:none;white-space:nowrap}
.nav a.active::after{content:"";position:absolute;left:0;right:0;bottom:-7px;height:2px;background:var(--white)}
.hero-art{left:600px;top:118px;width:600px;height:480px;background:radial-gradient(ellipse at 50% 45%,#7d6fe6 0%,#4b3fc0 30%,#2e2394 60%,rgba(33,24,122,0) 80%)}
.hero-trace{left:180px;top:380px;width:800px;height:210px;background:radial-gradient(ellipse at 50% 70%,rgba(62,195,207,.28) 0%,rgba(62,195,207,0) 65%)}
.hero-title{left:111px;top:250px;color:var(--white);font-size:41px;line-height:42px;font-weight:900;text-transform:uppercase}
.btn-cyan{background:var(--cyan);color:var(--white);font-weight:700;font-size:16px;border-radius:26px;display:flex;align-items:center;justify-content:center;text-transform:uppercase}
.hero-btn{left:111px;top:404px;width:200px;height:50px}
.slider-dot{left:1124px;width:12px;height:12px;border:2px solid var(--white);border-radius:50%}
.slider-dot.on{background:var(--white)}
.scroll-down{left:570px;top:588px;width:60px;height:60px;border-radius:50%;background:var(--white);display:flex;align-items:center;justify-content:center}

/* shared */
.frame-corner{width:120px;height:120px;border:4px solid var(--cyan);border-right:none;border-bottom:none;border-radius:12px 0 0 0}
.navy-block{background:var(--navy);border-radius:0 0 6px 6px}
.photo{border-radius:12px}
.dots{background-image:radial-gradient(circle,#d8d8e4 2px,transparent 2.5px);background-size:20px 20px}
.h2{font-size:40px;line-height:40px;font-weight:700;text-transform:uppercase;color:var(--ink)}
.center{text-align:center}

/* monitoring */
.mon-photo{left:144px;top:718px;width:438px;height:395px;background:linear-gradient(135deg,#1d5fa8 0%,#2f7fd0 40%,#1b3f7d 100%)}
.mon-title{left:641px;top:728px;width:460px}
.mon-text{left:641px;top:821px;width:448px;font-size:13px;line-height:25.7px;color:var(--body)}
.mon-list{left:641px;top:985px;list-style:none;font-size:16px;color:#333}
.mon-list li{height:29.5px;display:flex;align-items:center;gap:10px}
.mon-list li::before{content:"";width:10px;height:10px;border:2px solid var(--navy);border-radius:50%;background:radial-gradient(circle,var(--navy) 2px,transparent 2.5px)}

/* video */
.lavender{left:0;top:1600px;width:1200px;height:874px;background:var(--lavender)}
.video-title{left:0;top:1222px;width:1200px;font-size:31px;font-weight:500;text-transform:uppercase}
.video{left:164px;top:1289px;width:872px;height:472px;background:linear-gradient(135deg,#ededed 0%,#dedede 55%,#cfcfd6 100%);box-shadow:0 4px 14px rgba(0,0,0,.12)}
.play{left:570px;top:1495px;width:60px;height:60px;border-radius:50%;background:var(--navy);display:flex;align-items:center;justify-content:center}

/* risk */
.risk-title{left:0;top:1836px;width:1200px;font-size:38px;line-height:38px}
.risk-text{left:108px;top:1884px;width:984px;font-size:14.5px;line-height:27.3px;color:#333}
.card{top:2036px;height:342px;background:var(--white);box-shadow:0 2px 10px rgba(0,0,0,.1);text-align:center}
.card-icon{position:absolute;left:50%;top:40px;transform:translateX(-50%)}
.card h3{position:absolute;left:0;right:0;top:140px;font-size:27px;font-weight:500;color:var(--ink)}
.card p{position:absolute;left:30px;right:30px;top:184px;font-size:14px;line-height:26.7px;color:#333}
.card a{position:absolute;left:0;right:0;top:280px;font-size:16px;font-weight:500;color:var(--cyan);text-decoration:underline}
.card.active::after{content:"";position:absolute;left:0;right:0;bottom:0;height:7px;background:var(--navy);border-radius:3px}

/* protect */
.protect{left:0;top:2474px;width:1200px;height:301px;background:var(--navy)}
.protect-title{left:0;top:2547px;width:1200px;color:var(--white);font-size:38px;line-height:40px}
.protect-text{left:150px;top:2604px;width:900px;color:var(--white);font-size:14.5px;line-height:28px}
.protect-text .link{color:var(--white);text-decoration:underline}

/* about */
.about-photo{left:144px;top:2874px;width:438px;height:341px;background:linear-gradient(135deg,#0d3c8a 0%,#1e78c8 45%,#54b8e6 70%,#1a3f86 100%)}
.about-title{left:641px;top:2912px}
.about-text{left:641px;top:2962px;width:458px;font-size:15.5px;line-height:30px;color:var(--body)}

/* contact strip */
.strip{left:0;top:3312px;width:1200px;height:124px;background:#0f0f0f}
.strip-sep{top:3312px;width:1px;height:124px;background:#3a3a3a}
.strip-icon{width:58px;height:58px;border:2px solid var(--white);border-radius:50%;display:flex;align-items:center;justify-content:center}
.strip-text{color:var(--white);font-size:15px;line-height:22px}

/* footer */
.footer{left:0;top:3436px;width:1200px;height:311px;background:var(--footer)}
.footer-brand{left:111px;top:3480px;color:var(--white);font-size:25px;font-weight:700}
.social{top:3525px;width:40px;height:40px;border:1.5px solid var(--white);border-radius:50%}
.social::after{content:"";position:absolute;left:14px;top:14px;width:9px;height:9px;border-radius:50%;background:var(--white)}
.footer-h{color:var(--white);font-size:18px;font-weight:700;text-transform:uppercase}
.field{background:var(--white);border-radius:4px;color:#777;font-size:15px;padding:0 19px;display:flex;align-items:center}
.submit{left:456px;top:3667px;width:158px;height:51px}
.quick a{position:absolute;left:984px;color:var(--white);font-size:13.5px;text-decoration:none}
.base{left:0;top:3747px;width:1200px;height:64px;background:var(--footer-base);color:var(--white);font-size:15px;display:flex;align-items:center;justify-content:center}
</style>
</head>
<body>

<!-- HERO -->
<section class="abs hero">
  <div class="abs hero-trace" role="img" aria-label="Glowing circuit trace lines"></div>
  <div class="abs hero-art" role="img" aria-label="Isometric illustration of laptops connected to a central server chip"></div>
  <div class="abs topbar"></div>
  <div class="abs topbar-item" style="left:527px">
    <span class="topbar-icon"><svg width="14" height="14" viewBox="0 0 24 24" fill="#fff"><path d="M6.6 10.8a15 15 0 0 0 6.6 6.6l2.2-2.2a1 1 0 0 1 1-.25 11.4 11.4 0 0 0 3.6.57 1 1 0 0 1 1 1V20a1 1 0 0 1-1 1A17 17 0 0 1 3 4a1 1 0 0 1 1-1h3.5a1 1 0 0 1 1 1c0 1.25.2 2.450.57 3.57a1 1 0 0 1-.25 1z"/></svg></span>
    CALL US TODAY: +1 555 014 2290
  </div>
  <div class="abs topbar-sep"></div>
  <div class="abs topbar-item" style="left:822px">
    <span class="topbar-icon"><svg width="15" height="12" viewBox="0 0 24 18" fill="none" stroke="#fff" stroke-width="2"><rect x="1" y="1" width="22" height="16" rx="1"/><path d="M1 1l11 9 11-9"/></svg></span>
    Email: info@quillstonemonitor.com
  </div>
  <div class="abs brand">DOMAIN MONITORING</div>
  <nav class="nav">
    <a class="active" style="left:478px">HOME</a>
    <a style="left:573px">ABOUT</a>
    <a style="left:675px">WHAT IS THE RISK</a>
    <a style="left:863px">MONITORING</a>
    <a style="left:1012px">CONTACT</a>
  </nav>
  <h1 class="abs hero-title">Prevent attacks by<br>monitoring your<br>domains</h1>
  <div class="abs btn-cyan hero-btn">Get Started</div>
  <div class="abs slider-dot on" style="top:294px"></div>
  <div class="abs slider-dot" style="top:318px"></div>
  <div class="abs slider-dot" style="top:343px"></div>
  <div class="abs slider-dot" style="top:367px"></div>
</section>
<div class="abs scroll-down"><svg width="14" height="26" viewBox="0 0 14 26" fill="none" stroke="var(--navy)" stroke-width="2"><path d="M7 1v23M1 18l6 6 6-6"/></svg></div>

<!-- MONITORING -->
<div class="abs dots" style="left:4px;top:964px;width:190px;height:254px"></div>
<div class="abs frame-corner" style="left:130px;top:704px"></div>
<div class="abs navy-block" style="left:471px;top:1014px;width:124px;height:111px"></div>
<div class="abs photo mon-photo" role="img" aria-label="Photo of a woman working on a laptop in a server room"></div>
<h2 class="abs h2 mon-title">What else are we monitoring?</h2>
<p class="abs mon-text">Veltrane helps you understand when, where and how stolen or accidentally leaked information in dark web markets, forums, botnet logs, IRC, social media and other sources is exposed. Veltrane' s alerting service can also detect threats before they turn into incidents. Veltrane offers AI-driven dark web analysis, real-time threat alerts and pre-Attack threat indicators. Setup in minutes you will receive instant access to real-time reporting including:</p>
<ul class="abs mon-list">
  <li>Infrastructure exposure: IOT, Repos, Nimbra, Codevault &amp; more</li>
  <li>People exposure: Social media monitoring</li>
  <li>Ransomware exposure: leak &amp; credential monitoring</li>
  <li>Attack prevention: domain and certificate monitoring</li>
</ul>

<!-- VIDEO -->
<div class="abs lavender"></div>
<div class="abs dots" style="left:1032px;top:1512px;width:168px;height:84px"></div>
<h2 class="abs video-title center">Domain Monitoring Explainer Video</h2>
<div class="abs video" role="img" aria-label="Explainer video still showing computer monitors linked by a curved line"></div>
<div class="abs play"><svg width="22" height="24" viewBox="0 0 22 24"><path d="M3 2l17 10-17 10z" fill="#fff"/></svg></div>

<!-- RISK -->
<h2 class="abs h2 risk-title center">What is the risk?</h2>
<p class="abs risk-text center">Hackers use domain-based attacks, which are designed to trick users into submitting sensitive data or downloading dangerous files. This is often the case with phishing attacks. For example, domains can be registered that are very similar to one's own company, a customer or a supplier. Once a fraudulent domain is registered, the hackers try to lure the employee to the website. This can be done via e-mail, SMS (smishing), instant messaging. Social media and many other techniques succeed. A distinction is made between different types of attacks:</p>

<div class="abs card" style="left:111px;width:314px">
  <svg class="card-icon" width="100" height="82" viewBox="0 0 100 82" fill="none" stroke="var(--navy)" stroke-width="2.5">
    <circle cx="50" cy="41" r="37"/><ellipse cx="50" cy="41" rx="16" ry="37"/><path d="M13 41h74M18 22h64M18 60h64"/>
    <rect x="3" y="30" width="94" height="22" rx="3" fill="#fff" stroke="var(--cyan)"/>
    <text x="12" y="47" font-family="Roboto,sans-serif" font-size="15" font-weight="700" fill="var(--navy)" stroke="none">WWW</text>
    <circle cx="80" cy="40" r="5"/><path d="M84 44l5 5"/>
  </svg>
  <h3>Domain Spoofing</h3>
  <p>Here, a domain name is registered that resembles that of a trusted brand or organization. For example, the hacker</p>
  <a>LEARN MORE</a>
</div>
<div class="abs card active" style="left:444px;width:312px">
  <svg class="card-icon" width="100" height="88" viewBox="0 0 100 88" fill="none" stroke="var(--navy)" stroke-width="2.5">
    <rect x="5" y="12" width="86" height="72" rx="4"/><path d="M5 24h86"/>
    <circle cx="13" cy="18" r="1.5"/><circle cx="19" cy="18" r="1.5"/>
    <path d="M48 36l18 32H30z" stroke="var(--cyan)"/><path d="M48 47v10M48 61v2"/>
    <path d="M88 2v6M94 10l4-3M96 16h3"/>
  </svg>
  <h3>Homoglyphic Attack</h3>
  <p>This is a variant of domain spoofing. Again, a similar looking domain is registered to.</p>
  <a>LEARN MORE</a>
</div>
<div class="abs card" style="left:775px;width:314px">
  <svg class="card-icon" width="84" height="86" viewBox="0 0 84 86" fill="none" stroke="var(--navy)" stroke-width="2.5">
    <rect x="6" y="40" width="72" height="42" rx="3"/><path d="M6 72h72"/>
    <circle cx="42" cy="22" r="16" stroke="var(--cyan)"/><ellipse cx="42" cy="22" rx="9" ry="5"/><circle cx="42" cy="22" r="2"/>
    <path d="M16 50h22M16 58h14M50 50h18M50 58h18"/>
    <path d="M10 8v6M7 11h6M74 6v6M71 9h6"/>
  </svg>
  <h3>Typosquatting</h3>
  <p>cybercriminals may attempt to register a malicious domain by using a common misspelling of the target company's</p>
  <a>LEARN MORE</a>
</div>

<!-- PROTECT -->
<section class="abs protect"></section>
<h2 class="abs h2 protect-title center">How to protect yourself?</h2>
<p class="abs protect-text center">Our domain monitoring solution continuously monitors thousands of TLDs, gTLDs and ccTLDs. For searches, we offer the greatest flexibility in the market and cover ALL forms of attacks. Here are a few examples of search options that can be adopted as active alerts: <span class="link">https://wiki.veltrane.example/docs/domain_database_search.</span> All data can be <span class="link">analyzed</span> and <span class="link">exported</span>.</p>

<!-- ABOUT -->
<div class="abs frame-corner" style="left:130px;top:2861px"></div>
<div class="abs navy-block" style="left:471px;top:3123px;width:124px;height:103px"></div>
<div class="abs photo about-photo" role="img" aria-label="Digital globe with streams of binary code"></div>
<h2 class="abs h2 about-title">About Veltrane</h2>
<p class="abs about-text">Veltrane (company registration number CHE-000.418.962) was started in 2018 as a public limited company in Zug, Switzerland. Our analysts have long-standing relationships with various players on the Darknet. These personal relationships make it possible for Veltrane to repeatedly obtain the latest data leaks. Those unique data leaks are published by the press around the world.</p>

<!-- CONTACT STRIP -->
<section class="abs strip"></section>
<div class="abs strip-sep" style="left:462px"></div>
<div class="abs strip-sep" style="left:780px"></div>
<div class="abs strip-icon" style="left:156px;top:3345px"><svg width="20" height="28" viewBox="0 0 20 28" fill="#fff"><path d="M10 0a10 10 0 0 0-10 10c0 7.500 10 18 10 18s10-10.500 10-18A10 10 0 0 0 10 0zm0 14a4 4 0 1 1 0-8 4 4 0 0 1 0 8z"/></svg></div>
<div class="abs strip-text" style="left:232px;top:3339px">Address:<br>123 Avenue name, City name<br>10150, United States</div>
<div class="abs strip-icon" style="left:532px;top:3345px"><svg width="24" height="24" viewBox="0 0 24 24" fill="#fff"><path d="M6.6 10.8a15 15 0 0 0 6.6 6.6l2.2-2.2a1 1 0 0 1 1-.25 11.4 11.4 0 0 0 3.6.57 1 1 0 0 1 1 1V20a1 1 0 0 1-1 1A17 17 0 0 1 3 4a1 1 0 0 1 1-1h3.5a1 1 0 0 1 1 1c0 1.25.2 2.45.57 3.57a1 1 0 0 1-.25 1z"/></svg></div>
<div class="abs strip-text" style="left:607px;top:3350px">Phone:<br>+1 555 014 2290</div>
<div class="abs strip-icon" style="left:807px;top:3345px"><svg width="26" height="20" viewBox="0 0 24 18" fill="none" stroke="#fff" stroke-width="2"><rect x="1" y="1" width="22" height="16" rx="1"/><path d="M1 1l11 9 11-9"/></svg></div>
<div class="abs strip-text" style="left:882px;top:3350px">Email<br>info@quillstonemonitor.com</div>

<!-- FOOTER -->
<footer class="abs footer"></footer>
<div class="abs footer-brand">DOMAIN MONITORING</div>
<div class="abs social" style="left:150px" aria-label="Social profile"></div>
<div class="abs social" style="left:199px" aria-label="Social profile"></div>
<div class="abs social" style="left:248px" aria-label="Social profile"></div>
<div class="abs social" style="left:297px" aria-label="Social profile"></div>

<div class="abs footer-h" style="left:456px;top:3474px">Contact Us</div>
<div class="abs field" style="left:456px;top:3513px;width:223px;height:51px">Name</div>
<div class="abs field" style="left:688px;top:3513px;width:224px;height:51px">Email</div>
<div class="abs field" style="left:456px;top:3574px;width:456px;height:80px;align-items:flex-start;padding-top:14px">Message</div>
<div class="abs btn-cyan submit">Submit</div>

<div class="abs footer-h" style="left:984px;top:3474px">Quick Link</div>
<nav class="quick">
  <a style="top:3509px">Home</a>
  <a style="top:3536px">About</a>
  <a style="top:3563px">What Is The Risk</a>
  <a style="top:3589px">Monitoring</a>
  <a style="top:3615px">Contact</a>
</nav>

<div class="abs base">DOMAIN MONITORING &nbsp;© 2022 All Rights Reserved | Privacy Policy</div>

</body>
</html>
```